Mobile app for checking bus arrival

I would like to make the UI much more beautiful and modern. The app is an app to check bus arrival in Singapore.
See here: https://apps.veltrano.com/store/apps/details?id=com.ridoka&hl=en

Based on the question from designers:

1. The first screen shows the favorite bus stop. Each item shows location / street, the top one is the location, second line is the street name. And the number is the bus stop code.

2. Please download the app and try bus stop code with 07589 or 10079, for example. It will bring you to the next screen.

3. The pencil allow you to select color theme, for the list item, and the header.

4. On the second screen, it will show up the list of bus route that available on that bus stop.

5. When you tap on one of them it will show you the 2 subsequent arrival time.

6. Each of the arrival time has the information of availability seats available, seats not available, no more space. (we can use green, yellow, red, respectively).

7. Each of the arrival time has the WAB indicator (Wheelchair availability). Show as icon is preferred.

7. KLT and VOPN are the bus provider in Singapore. 48 means the route /service no.

Requirements:
And check the attachment, see screen 3. I need to add information about the space availability, which has 3 state: seats available, seats not available, no more space. (we can use green, yellow, red, respectively).

Please advise how to show the information.

Target Market(s)

Students, age below 35

Industry/Entity Type

Trivex

Requirements
Must have
• The app currently has the capabilities to select color theme, checkout screen1. It's the button and the list item color.
Nice to have
• Please download the app to see all available colors, and make suggestion to have better color pallete.

```html
<!DOCTYPE html>
<html lang="en">
<head>
<meta charset="utf-8">
<title>Bus Stop 07589 – Arrivals</title>
<link rel="stylesheet" href="https://fonts.googleapis.com/css2?family=Roboto:wght@300;400;500&display=swap">
<style>
  :root{
    --green:#5ccb5a;
    --green-light:#7ad678;
    --page:#f2f2f2;
    --white:#ffffff;
    --ink:#1c1c1c;
    --muted:#666666;
    --line:#dddddd;
    --dot-grey:#999999;
    --dot-green:#2fb54a;
    --dot-red:#e0313a;
    --dot-yellow:#f5bc00;
    --ad-dark:#3c3c3c;
  }
  *{box-sizing:border-box;margin:0;padding:0}
  html,body{width:676px;height:1200px;overflow:hidden;background:var(--page)}
  body{font-family:"Roboto",sans-serif}
  .screen{position:absolute;left:0;top:0;width:640px;height:1136px;transform:scale(1.05625);transform-origin:0 0;background:var(--page);overflow:hidden}
  .appbar{position:absolute;left:0;top:0;width:640px;height:128px;background:var(--green);color:var(--white)}
  .status{position:absolute;top:6px;left:0;width:640px;height:30px;font-size:21px;font-weight:500}
  .status .carrier{position:absolute;left:6px;top:2px;letter-spacing:.5px}
  .status .time{position:absolute;left:0;width:640px;text-align:center;top:2px}
  .status .battery-text{position:absolute;right:68px;top:2px}
  .status svg{position:absolute}
  .toolbar .stop-code{position:absolute;left:127px;top:74px;font-size:34px;font-weight:400;letter-spacing:1px}
  .toolbar svg{position:absolute}
  .location{position:absolute;left:0;top:128px;width:640px;height:96px;background:var(--green);color:var(--white);border-top:1px solid var(--green-light)}
  .location .pin-box{position:absolute;left:0;top:0;width:72px;height:96px;background:var(--green-light)}
  .location .stop-name{position:absolute;left:72px;right:0;top:8px;text-align:center;font-size:34px;font-weight:400}
  .location .street{position:absolute;left:72px;right:0;top:52px;text-align:center;font-size:20px}
  .connector{position:absolute;left:320px;top:357px;width:1px;height:245px;background:var(--line)}
  .card{position:absolute;left:24px;width:593px;background:var(--green);color:var(--white);box-shadow:0 2px 3px rgba(0,0,0,.18)}
  .card .service{text-align:center;font-weight:400}
  .card.open{top:250px;height:322px}
  .card.open .service{height:107px;line-height:107px;font-size:54px;letter-spacing:2px}
  .arrivals{position:absolute;top:107px;left:0;width:593px;height:215px;background:var(--white);display:flex}
  .arrival{position:relative;width:50%;height:215px;color:var(--ink)}
  .arrival+.arrival{border-left:1px solid var(--line)}
  .arrival .label{position:absolute;left:26px;top:44px;font-size:22px;color:var(--muted);display:flex;align-items:center;gap:6px}
  .arrival .eta{position:absolute;left:24px;top:92px;font-size:42px;font-weight:500}
  .arrival .wab{position:absolute;right:14px;top:88px}
  .arrival .load{position:absolute;left:0;right:0;top:149px;height:66px;border-top:1px solid var(--line);display:flex;justify-content:flex-end;align-items:center;gap:9px;padding-right:18px}
  .dot{width:21px;height:21px;border-radius:50%;background:var(--dot-grey)}
  .dot.green{background:var(--dot-green)}
  .dot.red{background:var(--dot-red)}
  .dot.yellow{background:var(--dot-yellow)}
  .card.closed{top:602px;height:320px}
  .card.closed .service{padding-top:98px;font-size:74px;font-weight:300;letter-spacing:3px}
  .card .operator{position:absolute;left:14px;bottom:10px;font-size:50px;font-weight:400;letter-spacing:2px}
  .card.peek{top:955px;height:200px}
  .ad{position:absolute;left:0;top:1048px;width:640px;height:88px;background:var(--ad-dark)}
  .ad .art{position:absolute;left:36px;top:0;width:570px;height:88px;background:linear-gradient(90deg,#6b4410 0%,#c98a1c 35%,#e8a62a 55%,#a8661a 80%,#5e3a0c 100%)}
  .ad .size{position:absolute;left:58px;top:10px;font-size:34px;color:var(--white);line-height:36px}
  .ad .brand{position:absolute;left:322px;top:18px;display:flex;align-items:center;gap:14px;color:var(--white)}
  .ad .brand-square{width:52px;height:52px;background:var(--white)}
  .ad .brand-name{font-size:34px}
  .ad .brand-name small{font-size:14px}
  .ad .info{position:absolute;left:6px;bottom:6px;width:24px;height:24px;border-radius:50%;background:#777;color:#ddd;font-size:16px;text-align:center;line-height:24px}
</style>
</head>
<body>
<div class="screen">
  <header class="appbar">
    <div class="status">
      <span class="carrier">●●●○○ TELVA</span>
      <svg style="left:160px;top:4px" width="26" height="20" viewBox="0 0 26 20"><path d="M13 18 L2 6 A16 16 0 0 1 24 6 Z" fill="#fff"/></svg>
      <span class="time">4:21 PM</span>
      <svg style="left:492px;top:2px" width="16" height="26" viewBox="0 0 16 26"><path d="M2 7 L13 18 L8 23 V3 L13 8 L2 19" fill="none" stroke="#b8ebb6" stroke-width="2"/></svg>
      <span class="battery-text">22%</span>
      <svg style="left:578px;top:4px" width="56" height="24" viewBox="0 0 56 24"><rect x="1" y="1" width="48" height="22" rx="3" fill="none" stroke="#fff" stroke-width="2"/><rect x="4" y="4" width="10" height="16" fill="#fff"/><rect x="50" y="8" width="4" height="8" fill="#fff"/></svg>
    </div>
    <div class="toolbar">
      <svg style="left:30px;top:72px" width="38" height="34" viewBox="0 0 38 34"><path d="M36 17H4 M18 3 L4 17 L18 31" fill="none" stroke="#fff" stroke-width="4"/></svg>
      <span class="stop-code">07589</span>
      <svg style="left:456px;top:66px" width="44" height="42" viewBox="0 0 24 23"><path d="M12 0l3.1 7.6 8.2.6-6.3 5.3 2 8-7-4.4-7 4.4 2-8L.7 8.2l8.2-.6z" fill="#fff"/></svg>
      <svg style="left:526px;top:68px" width="42" height="42" viewBox="0 0 24 24"><path d="M19 12a7 7 0 1 1-2.2-5.1" fill="none" stroke="#fff" stroke-width="3.4"/><path d="M13 2 L21 2 L21 10 Z" fill="#fff"/></svg>
      <svg style="left:594px;top:70px" width="12" height="36" viewBox="0 0 12 36"><circle cx="6" cy="5" r="4" fill="#fff"/><circle cx="6" cy="18" r="4" fill="#fff"/><circle cx="6" cy="31" r="4" fill="#fff"/></svg>
    </div>
  </header>

  <section class="location">
    <div class="pin-box">
      <svg style="position:absolute;left:24px;top:34px" width="24" height="30" viewBox="0 0 24 30"><path d="M12 28 C4 18 2 14 2 10 A10 10 0 0 1 22 10 C22 14 20 18 12 28Z" fill="none" stroke="#fff" stroke-width="2.4"/><circle cx="12" cy="10" r="3.4" fill="none" stroke="#fff" stroke-width="2.4"/></svg>
    </div>
    <div class="stop-name">Opp varden ctr</div>
    <div class="street">varden rd</div>
  </section>

  <div class="connector"></div>

  <article class="card open">
    <div class="service">120</div>
    <div class="arrivals">
      <div class="arrival">
        <div class="label"><svg width="32" height="32" viewBox="0 0 32 32"><circle cx="16" cy="16" r="13.5" fill="none" stroke="#666" stroke-width="2.6"/><path d="M16 8V17L22 21" fill="none" stroke="#666" stroke-width="2.6"/></svg>Arrival Time</div>
        <div class="eta">7 mins</div>
        <svg class="wab" width="34" height="48" viewBox="0 0 34 48" role="img" aria-label="Wheelchair accessible"><path d="M5 2 L9 12" stroke="#1c1c1c" stroke-width="4"/><circle cx="16" cy="29" r="12" fill="none" stroke="#1c1c1c" stroke-width="6"/><circle cx="16" cy="29" r="3" fill="#1c1c1c"/><path d="M28 24 L32 42" stroke="#1c1c1c" stroke-width="4"/></svg>
        <div class="load"><span class="dot green"></span><span class="dot"></span><span class="dot"></span></div>
      </div>
      <div class="arrival">
        <div class="label"><svg width="32" height="32" viewBox="0 0 32 32"><circle cx="16" cy="16" r="13.5" fill="none" stroke="#666" stroke-width="2.6"/><path d="M16 8V17L22 21" fill="none" stroke="#666" stroke-width="2.6"/></svg>Arrival Time</div>
        <div class="eta">21 mins</div>
        <svg class="wab" width="34" height="48" viewBox="0 0 34 48" role="img" aria-label="Wheelchair not confirmed"><path d="M5 2 L9 12" stroke="#888" stroke-width="4"/><circle cx="16" cy="29" r="12" fill="none" stroke="#888" stroke-width="6"/><circle cx="16" cy="29" r="3" fill="#888"/><path d="M28 24 L32 42" stroke="#888" stroke-width="4"/></svg>
        <div class="load"><span class="dot"></span><span class="dot red"></span><span class="dot yellow"></span></div>
      </div>
    </div>
  </article>

  <article class="card closed">
    <div class="service">147</div>
    <div class="operator">KLT</div>
  </article>

  <article class="card peek"></article>

  <aside class="ad">
    <div class="art" role="img" aria-label="Golden ornamental banner background"></div>
    <div class="size">320x50<br>Test Banner</div>
    <div class="brand"><span class="brand-square"></span><span class="brand-name">AdNest <small>by Trivex</small></span></div>
    <div class="info">i</div>
  </aside>
</div>
</body>
</html>
```